My project benefits Military, First Responders, Police, Fire, and Educators.

Contact Information for Business Card

2 Sided appointment card. Visual side will have my head shot with "Brisk Lantern" in a bold graffic/text. I am picturing maybe the headshot applied to a filter that has a matrix effect where the picture is made up of data/numbers flowing vertically through the photo. I am of course open to other concepts as well. Side two will have contact info presented in an attractive visual complimenting the front.

```html
<!DOCTYPE html>
<html lang="en">
<head>
<meta charset="utf-8">
<title>Brisk Lantern – Appointment Card</title>
<link rel="stylesheet" href="https://fonts.googleapis.com/css2?family=Orbitron:wght@500;700&family=Russo+One&display=swap">
<style>
  :root {
    --bg: #5a5a5a;
    --card: #000000;
    --green: #8ed13c;
    --green-deep: #0f3a12;
    --green-mid: #1f6b22;
    --green-glow: #2f8a2c;
  }
  html, body {
    margin: 0;
    width: 1200px;
    height: 1200px;
    overflow: hidden;
    background: var(--bg);
  }
  .canvas {
    position: relative;
    width: 1200px;
    height: 1200px;
  }
  .card {
    position: absolute;
    top: 256px;
    width: 394px;
    height: 688px;
    background: var(--card);
    overflow: hidden;
    box-shadow: 0 6px 16px rgba(0,0,0,0.45);
  }
  .card--contact { left: 171px; }
  .card--visual { left: 637px; }

  .code-rain {
    position: absolute;
    left: 0; top: 0;
    width: 100%;
    height: 380px;
    background:
      radial-gradient(ellipse 220px 160px at 200px 120px, rgba(31,107,34,0.45) 0%, rgba(0,0,0,0) 100%),
      linear-gradient(to bottom, #0c2e0e 0%, #092309 45%, #041104 78%, var(--card) 100%);
  }
  .circuit {
    position: absolute;
    left: 0; top: 0;
    width: 394px;
    height: 688px;
  }
  .contact-text {
    position: absolute;
    margin: 0;
    color: var(--green);
    font-family: "Orbitron", sans-serif;
    font-weight: 500;
    white-space: nowrap;
    line-height: 1;
  }
  .contact-name {
    left: 60px; top: 190px;
    font-size: 37px;
    font-weight: 700;
  }
  .contact-phone { left: 154px; top: 318px; font-size: 20px; }
  .contact-email { left: 69px; top: 369px; font-size: 21px; }
  .contact-experience { left: 62px; top: 450px; font-size: 21px; }
  .audience {
    position: absolute;
    left: 146px; top: 549px;
    margin: 0; padding: 0;
    list-style: none;
    color: var(--green);
    font-family: "Orbitron", sans-serif;
    font-weight: 500;
    font-size: 18.5px;
    line-height: 26.5px;
    white-space: nowrap;
  }

  .portrait {
    position: absolute;
    left: 0; top: 0;
    width: 100%;
    height: 600px;
    background:
      radial-gradient(ellipse 120px 170px at 215px 160px, var(--green-glow) 0%, rgba(31,107,34,0.5) 55%, rgba(0,0,0,0) 100%),
      radial-gradient(ellipse 200px 260px at 200px 360px, rgba(31,107,34,0.35) 0%, rgba(0,0,0,0) 100%),
      linear-gradient(to bottom, #0d300f 0%, #0b2a0d 60%, #041004 90%, var(--card) 100%);
  }
  .brand-name {
    position: absolute;
    left: 0; right: 0;
    top: 585px;
    margin: 0;
    text-align: center;
    color: var(--green);
    font-family: "Russo One", sans-serif;
    font-weight: 400;
    font-size: 35px;
    letter-spacing: 0.5px;
    line-height: 1;
  }
</style>
</head>
<body>
<main class="canvas">

  <section class="card card--contact">
    <div class="code-rain" role="img" aria-label="Falling green digital code characters in vertical streams"></div>

    <svg class="circuit" viewBox="0 0 394 688" aria-hidden="true">
      <g fill="none" stroke="#8ed13c" stroke-width="1.6">
        <polyline points="333,208 333,256 0,256"/>
        <polyline points="219,256 219,291 350,291 350,356 74,356"/>
        <polyline points="0,276 159,276 159,306"/>
        <polyline points="29,276 29,416 198,416 198,438"/>
        <circle cx="83" cy="602" r="42" stroke-width="2.4"/>
        <circle cx="83" cy="602" r="33" stroke-width="1.6"/>
        <line x1="83" y1="542" x2="83" y2="662"/>
        <line x1="23" y1="602" x2="143" y2="602"/>
      </g>
      <g fill="#8ed13c">
        <circle cx="333" cy="208" r="5.5"/>
        <circle cx="159" cy="306" r="5.5"/>
        <circle cx="74" cy="356" r="5.5"/>
        <circle cx="198" cy="438" r="5.5"/>
      </g>
    </svg>

    <h1 class="contact-text contact-name">Dale Corwin</h1>
    <p class="contact-text contact-phone">555-210-4477</p>
    <p class="contact-text contact-email">dcorwin@mail.com</p>
    <p class="contact-text contact-experience">14 years of experience</p>

    <ul class="audience">
      <li>Military,</li>
      <li>Law Enforcement,</li>
      <li>First Responders,</li>
      <li>&amp; Educators.</li>
    </ul>
  </section>

  <section class="card card--visual">
    <div class="portrait" role="img" aria-label="Headshot portrait in green tones built from vertical streams of falling digital code"></div>
    <h2 class="brand-name">BRISK LANTERN</h2>
  </section>

</main>
</body>
</html>
```